Business card for a Exhibition booth fabrication company

Hi. My company would like to change our corporate name card. We are an events and Exhibition stand builder company. We would like our corporate name card to resonate what we do. I need someone to create something unique that relates to the industry that I am in. The graphic designer should be creative to incorporate the elements of my industry and try to blend in well in the design of the card. Our aim is to ensure that we are unique and our card can look different from our competitors.
Updates

Target Market(s)

Marketing and events manager from all companies

Contact Information for Business Card

The business card should have the following details:
Name
Job Title
Email
Website

Colors

Designer to choose colors to be used in the design.

Requirements
Must have
• The card must be look something that is relevant to the service that I am providing. My website is: www.velmora-buildworks.com
• You can see my website to get more information on what service that I am doing
Nice to have
• On the back of my card, I would like to have a globe image with the incorporation of my company logo. This is to indicate that my services can be done in any part of the world.

```html
<!DOCTYPE html>
<html lang="en">
<head>
<meta charset="utf-8">
<title>Velmora Buildworks – Business Card</title>
<link rel="stylesheet" href="https://fonts.googleapis.com/css2?family=Arimo:wght@400;700&family=Open+Sans:wght@400&display=swap">
<style>
  :root {
    --stage: #1e1e20;
    --card-white: #ffffff;
    --brand-red: #ec1c24;
    --brand-green: #0b7a3a;
    --globe-light: rgba(120, 190, 145, 0.55);
    --globe-mid: rgba(80, 165, 112, 0.35);
    --ink-grey: #6b6b6b;
    --silver: #d9dbdb;
    --curve-grey: #7a7a7a;
  }
  * { margin: 0; padding: 0; box-sizing: border-box; }
  html, body { width: 1200px; height: 960px; overflow: hidden; }
  body {
    background: var(--stage);
    position: relative;
    font-family: "Arimo", Arial, sans-serif;
  }
  .card {
    position: absolute;
    left: 230px;
    width: 740px;
    height: 423px;
    overflow: hidden;
    border-radius: 4px;
  }

  /* Back side: globe / world reach */
  .card-back { top: 30px; background: var(--brand-green); }
  .globe-area {
    position: absolute;
    left: 70px; top: 18px;
    width: 650px; height: 360px;
    border-radius: 50% / 46%;
    background:
      radial-gradient(ellipse at 30% 40%, var(--globe-light) 0%, rgba(0,0,0,0) 38%),
      radial-gradient(ellipse at 72% 48%, var(--globe-light) 0%, rgba(0,0,0,0) 40%),
      radial-gradient(ellipse at 50% 50%, var(--globe-mid) 0%, rgba(11,122,58,0) 72%);
  }
  .back-brand {
    position: absolute;
    left: 0; right: 0; top: 176px;
    text-align: center;
    font-weight: 700;
    font-size: 32px;
    letter-spacing: 4px;
    color: var(--silver);
  }
  .back-brand .dot {
    display: inline-block;
    width: 22px; height: 22px;
    border-radius: 50%;
    background: var(--silver);
    margin-right: 14px;
    vertical-align: -1px;
  }
  .back-web {
    position: absolute;
    left: 0; right: 0; top: 262px;
    text-align: center;
    font-family: "Open Sans", Arial, sans-serif;
    font-size: 20px;
    letter-spacing: 4px;
    color: var(--card-white);
  }

  /* Front side */
  .card-front { top: 503px; background: var(--card-white); }
  .card-front svg.sweep { position: absolute; left: 0; top: 0; }
  .front-brand {
    position: absolute;
    left: 48px; top: 70px;
    font-weight: 700;
    font-size: 27px;
    letter-spacing: 2px;
    color: var(--ink-grey);
  }
  .front-brand .dot {
    display: inline-block;
    width: 20px; height: 20px;
    border-radius: 50%;
    background: var(--brand-red);
    margin-right: 12px;
    vertical-align: -1px;
  }
  .person {
    position: absolute;
    right: 48px; top: 132px;
    text-align: right;
  }
  .person-name {
    font-weight: 700;
    font-size: 25px;
    letter-spacing: 1px;
    color: var(--brand-red);
  }
  .person-title {
    font-size: 18px;
    letter-spacing: 1px;
    color: var(--ink-grey);
    margin-top: 4px;
  }
  .contacts {
    position: absolute;
    right: 40px; top: 274px;
    list-style: none;
    font-family: "Open Sans", Arial, sans-serif;
    font-size: 17px;
    color: var(--card-white);
    line-height: 30px;
  }
  .contacts li { display: flex; justify-content: flex-end; align-items: center; gap: 10px; }
  .contacts svg { width: 16px; height: 16px; flex: none; }
</style>
</head>
<body>

<section class="card card-back" aria-label="Business card back">
  <div class="globe-area" role="img" aria-label="Faint world map globe showing that stands are built anywhere in the world"></div>
  <div class="back-brand"><span class="dot"></span>VELMORA BUILDWORKS</div>
  <div class="back-web">www.velmora-buildworks.com</div>
</section>

<section class="card card-front" aria-label="Business card front">
  <svg class="sweep" width="740" height="423" viewBox="0 0 740 423" aria-hidden="true">
    <path d="M0,222 Q240,170 500,205 Q640,225 740,262" fill="none" stroke="var(--curve-grey)" stroke-width="6"/>
    <path d="M0,238 Q240,186 500,222 Q640,242 740,280 L740,423 L0,423 Z" fill="var(--brand-red)"/>
  </svg>

  <div class="front-brand"><span class="dot"></span>VELMORA BUILDWORKS</div>

  <div class="person">
    <div class="person-name">MARCUS HALE</div>
    <div class="person-title">PRESIDENT</div>
  </div>

  <ul class="contacts">
    <li>012-555-0148
      <svg viewBox="0 0 16 16" aria-hidden="true"><path d="M3.5 1.5l2.5 2.8-1.3 1.6c.8 1.9 2.2 3.4 4.2 4.3l1.6-1.3 2.9 2.4-1.4 2.3C6.9 13.5 2.5 9.1 1.3 3z" fill="#fff"/></svg>
    </li>
    <li>info@velmora-buildworks.com
      <svg viewBox="0 0 16 16" aria-hidden="true"><rect x="1" y="3.5" width="14" height="9" fill="#fff"/><path d="M1 3.5l7 5 7-5" fill="none" stroke="var(--brand-red)" stroke-width="1.2"/></svg>
    </li>
    <li>www.velmora-buildworks.com
      <svg viewBox="0 0 16 16" aria-hidden="true"><g fill="none" stroke="#fff" stroke-width="1.2"><circle cx="8" cy="8" r="6.5"/><ellipse cx="8" cy="8" rx="3" ry="6.5"/><path d="M1.5 8h13M2.5 4.8h11M2.5 11.2h11"/></g></svg>
    </li>
    <li>Street Name, City Name, Zipcode - 01234</li>
  </ul>
</section>

</body>
</html>
```